Flyer für Immobilienmakler
Zielgruppe
Wir, die Kessler Immobilien GmbH, vermitteln Häuser, Wohnungen und Grundstücke, unsere Zielgruppe sind Verkäufer und Kaufinteressenten aus der Region, Immobilien zur Vermittlung gesucht
Aufgabenstellung
Unverbindliche Ersteinschätzung, Ansprechpartner vor Ort, regionale Marktkenntnis. Max. Din A 5, Immobilien zur Vermittlung gesucht.
- Flyer nur zur Immobilienvermittlung

```html
<!DOCTYPE html>
<html lang="de">
<head>
<meta charset="utf-8">
<title>Kessler Immobilien GmbH – Flyer</title>
<link rel="stylesheet" href="https://fonts.googleapis.com/css2?family=Oswald:wght@700&family=Montserrat:wght@400;500;700;800&display=swap">
<style>
  :root {
    --ink: #1f1c1e;
    --purple: #6a4fa3;
    --purple-dark: #4a3478;
    --green: #129c6f;
    --black: #000000;
    --white: #ffffff;
    --page: #e9e6e1;
    --sky: #9cc8ea;
    --house: #8a8078;
    --lawn: #6f9a4a;
    --office: #b9aea3;
  }
  * { margin: 0; padding: 0; box-sizing: border-box; }
  html, body { width: 1200px; height: 1117px; overflow: hidden; background: var(--page); }
  .stage { position: relative; width: 1200px; height: 1117px; }
  .flyer {
    position: absolute; left: 226px; top: 30px;
    width: 1058px; height: 1494px;
    background: var(--white);
    transform: scale(0.7075); transform-origin: top left;
    font-family: "Montserrat", sans-serif; color: var(--ink);
    overflow: hidden;
    box-shadow: 0 10px 30px rgba(0,0,0,.18);
  }
  .shapes { position: absolute; inset: 0; }
  .headline {
    position: absolute; left: 78px; top: 90px; width: 610px;
    font-family: "Oswald", sans-serif; font-weight: 700;
    font-size: 64px; line-height: 60px; letter-spacing: -0.6px;
    text-transform: uppercase; white-space: nowrap;
    transform: scaleY(1.12); transform-origin: top left;
  }
  .headline .accent { color: var(--purple); display: block; }
  .benefits {
    position: absolute; left: 750px; top: 66px; list-style: none;
    color: var(--white); font-weight: 800; font-size: 21px; line-height: 27px;
    text-transform: uppercase;
  }
  .benefits li { position: relative; padding-left: 30px; margin-bottom: 18px; }
  .tick { position: absolute; left: 0; top: 4px; width: 19px; height: 19px; }
  .about { position: absolute; left: 80px; top: 688px; width: 420px; }
  .about h2 { color: var(--green); font-size: 28px; font-weight: 700; margin-bottom: 4px; }
  .about p { font-size: 19px; line-height: 25.6px; font-weight: 400; }
  .services {
    position: absolute; left: 568px; top: 690px; width: 440px; color: var(--white);
  }
  .services h2 {
    font-family: "Oswald", sans-serif; font-weight: 700; font-size: 37px;
    text-transform: uppercase; margin-bottom: 14px; letter-spacing: -0.3px;
  }
  .services ul { list-style: none; }
  .services li { position: relative; margin-bottom: 16px; }
  .services h3 { font-size: 21px; font-weight: 700; padding-left: 26px; line-height: 27px; white-space: nowrap; }
  .services p { font-size: 19px; line-height: 25.6px; padding-left: 32px; font-weight: 400; }
  .services .tick { top: 4px; width: 18px; height: 18px; }
  .contact {
    position: absolute; left: 88px; top: 1282px; color: var(--white); list-style: none;
    font-weight: 700; font-size: 20px;
  }
  .contact li { display: flex; align-items: center; gap: 16px; height: 34px; }
  .contact li.phone { font-family: "Oswald", sans-serif; font-size: 44px; height: 62px; gap: 18px; }
  .contact svg { width: 24px; height: 24px; flex: none; }
  .brand {
    position: absolute; left: 560px; top: 1410px; width: 470px;
    display: flex; align-items: center; justify-content: center; gap: 12px;
    font-size: 26px; font-weight: 500; color: var(--ink);
  }
  .brand .mark { width: 14px; height: 14px; background: var(--green); }
</style>
</head>
<body>
<div class="stage">
  <article class="flyer">
    <svg class="shapes" viewBox="0 0 1058 1494" width="1058" height="1494">
      <defs>
        <linearGradient id="street" x1="0" y1="0" x2="0" y2="1">
          <stop offset="0" stop-color="var(--sky)"/>
          <stop offset="0.45" stop-color="var(--house)"/>
          <stop offset="0.85" stop-color="var(--lawn)"/>
          <stop offset="1" stop-color="#9a9a9a"/>
        </linearGradient>
        <linearGradient id="office" x1="0" y1="0" x2="1" y2="1">
          <stop offset="0" stop-color="#d9d4cf"/>
          <stop offset="0.6" stop-color="var(--office)"/>
          <stop offset="1" stop-color="#6e6660"/>
        </linearGradient>
      </defs>
      <polygon class="benefit-panel" points="715,0 1058,0 1058,327 715,295" fill="var(--green)"/>
      <polygon class="hero-photo" role="img" aria-label="Foto: Straße mit neuen Einfamilienhäusern, Bäumen und Rasen unter blauem Himmel" points="0,245 1058,342 1058,750 0,650" fill="url(#street)"/>
      <polygon class="contact-band" points="0,1138 530,1190 788,1284 530,1348 530,1494 0,1494" fill="var(--black)"/>
      <polygon class="team-photo-frame" points="72,945 530,988 530,1260 72,1216" fill="var(--white)"/>
      <polygon class="team-photo" role="img" aria-label="Foto: Beratungsgespräch am Tisch im hellen Büro" points="79,949 530,990 530,1250 79,1208" fill="url(#office)"/>
      <polygon class="services-fold" points="478,695 530,630 530,695" fill="var(--purple-dark)"/>
      <polygon class="services-panel" points="530,630 1035,677 1035,1306 530,1258" fill="var(--purple)"/>
    </svg>

    <h1 class="headline">Ihr Immobilienprofi<span class="accent">in Tann &amp; Umgebung</span></h1>

    <ul class="benefits">
      <li><svg class="tick" viewBox="0 0 20 20"><circle cx="10" cy="10" r="10" fill="#fff"/><path d="M5.5 10.3l3 3 6-6.3" stroke="var(--green)" stroke-width="2.6" fill="none"/></svg>Unverbindliche<br>Ersteinschätzung</li>
      <li><svg class="tick" viewBox="0 0 20 20"><circle cx="10" cy="10" r="10" fill="#fff"/><path d="M5.5 10.3l3 3 6-6.3" stroke="var(--green)" stroke-width="2.6" fill="none"/></svg>Ansprechpartner<br>vor Ort</li>
      <li><svg class="tick" viewBox="0 0 20 20"><circle cx="10" cy="10" r="10" fill="#fff"/><path d="M5.5 10.3l3 3 6-6.3" stroke="var(--green)" stroke-width="2.6" fill="none"/></svg>Regionale<br>Marktkenntnis</li>
    </ul>

    <section class="about">
      <h2>Über Uns</h2>
      <p>Kessler Immobilien GmbH ist Ihr erfahrener Partner für die Vermittlung von Häusern, Wohnungen und Grundstücken in der Region. Wir begleiten Verkäufer und Kaufinteressenten persönlich und professionell – von der ersten Einschätzung bis zum erfolgreichen Abschluss.</p>
    </section>

    <section class="services">
      <h2>Unsere Leistungen</h2>
      <ul>
        <li><svg class="tick" viewBox="0 0 20 20"><circle cx="10" cy="10" r="10" fill="#fff"/><path d="M5.5 10.3l3 3 6-6.3" stroke="var(--purple)" stroke-width="2.6" fill="none"/></svg><h3>Immobilienvermittlung</h3><p>Vermittlung von Häusern, Wohnungen und Gewerbeimmobilien – zuverlässig und diskret.</p></li>
        <li><svg class="tick" viewBox="0 0 20 20"><circle cx="10" cy="10" r="10" fill="#fff"/><path d="M5.5 10.3l3 3 6-6.3" stroke="var(--purple)" stroke-width="2.6" fill="none"/></svg><h3>Wertermittlung &amp; Ersteinschätzung</h3><p>Unverbindliche Einschätzung Ihrer Immobilie auf Basis regionaler Marktdaten – kostenfrei und transparent.</p></li>
        <li><svg class="tick" viewBox="0 0 20 20"><circle cx="10" cy="10" r="10" fill="#fff"/><path d="M5.5 10.3l3 3 6-6.3" stroke="var(--purple)" stroke-width="2.6" fill="none"/></svg><h3>Grundstücksvermittlung</h3><p>Unterstützung beim Verkauf von Bauland, Grundstücken und landwirtschaftlichen Flächen.</p></li>
        <li><svg class="tick" viewBox="0 0 20 20"><circle cx="10" cy="10" r="10" fill="#fff"/><path d="M5.5 10.3l3 3 6-6.3" stroke="var(--purple)" stroke-width="2.6" fill="none"/></svg><h3>Immobilien gesucht</h3><p>Sie möchten verkaufen? Wir suchen Häuser, Wohnungen und Grundstücke für vorgemerkte Käufer.</p></li>
      </ul>
    </section>

    <ul class="contact">
      <li class="phone"><svg viewBox="0 0 24 24"><path d="M6.6 2.5l3 3.6-2 2.4a14 14 0 0 0 7.9 7.9l2.4-2 3.6 3-1.8 3.6C11 20.5 3.5 13 3 4.3z" fill="var(--green)"/></svg>+49 85 72 555120-0</li>
      <li><svg viewBox="0 0 24 24"><circle cx="12" cy="12" r="11" fill="var(--green)"/><rect x="6.5" y="8" width="11" height="8" fill="none" stroke="#000" stroke-width="1.4"/><path d="M6.5 8.5l5.5 4 5.5-4" fill="none" stroke="#000" stroke-width="1.4"/></svg>info@kessler-immobilien.de</li>
      <li><svg viewBox="0 0 24 24"><circle cx="12" cy="12" r="11" fill="var(--green)"/><circle cx="12" cy="12" r="6" fill="none" stroke="#000" stroke-width="1.3"/><path d="M6 12h12M12 6c-3 3.5-3 8.5 0 12M12 6c3 3.5 3 8.5 0 12" fill="none" stroke="#000" stroke-width="1.3"/></svg>www.kessler-immobilien.de</li>
      <li><svg viewBox="0 0 24 24"><path d="M12 1.5a7.5 7.5 0 0 0-7.5 7.5c0 5.6 7.5 13.5 7.5 13.5s7.5-7.9 7.5-13.5A7.5 7.5 0 0 0 12 1.5z" fill="var(--green)"/><circle cx="12" cy="9" r="3" fill="#000"/></svg>Lindenweg 7, 84367 Tann</li>
    </ul>

    <div class="brand"><span class="mark"></span>Kessler Immobilien GmbH</div>
  </article>
</div>
</body>
</html>
```